E learning Platform for privacy

Current website is as below and its more of a shell.
I need someone to take the text and content and design it properly.
https://study.vornaquill.com/

After that, design has to be implemented with elementor and wordpress
https://elementor.com/

```html
<!DOCTYPE html>
<html lang="en">
<head>
<meta charset="utf-8">
<title>Vorna Learning Centre</title>
<link href="https://fonts.googleapis.com/css2?family=Raleway:ital,wght@0,400;0,500;0,600;0,700;0,800;1,400&display=swap" rel="stylesheet">
<style>
:root{
  --orange:#e8582a;
  --amber:#f39a2a;
  --ink:#1c1c1c;
  --text:#3a3a3a;
  --muted:#6b6b6b;
  --night:#0d1a2b;
  --black:#0b0b0b;
  --white:#ffffff;
}
*{box-sizing:border-box;margin:0;padding:0}
html,body{width:1200px;height:4159px;overflow:hidden}
body{position:relative;background:var(--white);font-family:"Raleway",sans-serif;color:var(--text)}
.abs{position:absolute}

/* header */
.site-header{position:absolute;left:0;top:0;width:1200px;height:83px;background:var(--white)}
.brand{position:absolute;left:88px;top:14px;font-weight:800;font-size:38px;letter-spacing:4px;color:var(--orange)}
.brand-small{font-size:30px;letter-spacing:3px}
.nav a{position:absolute;top:33px;font-size:16px;color:var(--ink);text-decoration:none}
.nav .active{color:var(--orange)}
.nav .sep{position:absolute;left:1000px;top:31px;font-size:16px;color:var(--ink)}

/* hero */
.hero{position:absolute;left:0;top:83px;width:1200px;height:560px;background:linear-gradient(120deg,#9a9a98 0%,#bdbcb8 45%,#a9a8a4 100%);border-bottom-right-radius:240px;overflow:hidden}
.hero-photo{position:absolute;left:680px;top:0;width:520px;height:560px;background:linear-gradient(160deg,#cfcdca,#8c8a86);border-top-left-radius:260px;border-bottom-left-radius:20px}
.hero-title{position:absolute;left:90px;top:381px;font-size:27px;font-weight:500;line-height:35px;color:#111}
.btn{position:absolute;display:flex;align-items:center;justify-content:center;gap:8px;background:var(--orange);color:var(--white);border-radius:30px;font-weight:600;text-decoration:none}
.hero .btn{left:90px;top:473px;width:192px;height:54px;font-size:19px;box-shadow:0 4px 10px rgba(0,0,0,.2)}

/* why section */
.section-title{position:absolute;left:0;width:1200px;text-align:center;font-weight:700;color:var(--ink)}
.section-title em{font-style:normal;color:var(--orange)}
.feature{position:absolute;width:322px;height:337px;background:var(--white);box-shadow:0 2px 12px rgba(0,0,0,.09);padding:30px 14px 0 15px}
.feature svg{display:block;height:56px}
.feature h3{margin-top:22px;font-size:22px;font-weight:500;line-height:29px;color:var(--ink)}
.feature p{margin-top:26px;font-size:14.5px;line-height:25px;color:var(--text)}

/* stats */
.stats-band{position:absolute;left:0;top:1685px;width:1200px;height:382px;background:linear-gradient(100deg,#25364e 0%,#0f1d33 55%,#050b16 100%);border-top-left-radius:300px 260px;border-bottom-right-radius:170px 170px}
.stats-band h2{position:absolute;top:64px;width:100%;text-align:center;font-size:36px;font-weight:700;color:var(--white)}
.stats-band p{position:absolute;top:124px;left:160px;width:880px;text-align:center;font-size:15px;line-height:27px;color:#e4e8ef}
.stat{position:absolute;width:292px;height:292px;border-radius:50%;background:linear-gradient(160deg,#f08a2a,#e8582a);color:var(--white);text-align:center;box-shadow:0 0 0 3px var(--white),0 6px 0 3px var(--orange)}
.stat b{display:block;margin-top:92px;font-size:66px;font-weight:700;line-height:70px}
.stat span{display:block;margin-top:8px;font-size:18px;letter-spacing:1px}

/* courses */
.course{position:absolute;top:2347px;width:294px;height:443px;color:var(--white);overflow:hidden}
.course-img{height:230px}
.course h3{margin:22px 0 0 22px;font-size:22px;font-weight:700;line-height:27px}
.course .rule{margin:18px 0 0 22px;width:30px;height:3px;background:var(--white)}
.course .price{margin:22px 0 0 22px;font-size:15px;font-weight:600}
.course .meta{margin:6px 0 0 22px;font-size:13px;line-height:22px}
.dot{position:absolute;top:2823px;width:9px;height:9px;border-radius:50%;background:var(--orange)}

/* testimonials */
.testimonials{position:absolute;left:0;top:2917px;width:1200px;height:476px;background:linear-gradient(120deg,#e05a24,#ea6a2e 60%,#d9521f);border-top-left-radius:140px 110px}
.testimonials h2{position:absolute;top:96px;width:100%;text-align:center;font-size:36px;font-weight:700;color:var(--white)}
.portrait{position:absolute;left:89px;top:158px;width:216px;height:216px;border-radius:50%;background:linear-gradient(160deg,#b58b6e,#6d5646);border:3px solid var(--white)}
.quote{position:absolute;left:334px;top:183px;width:700px;font-style:italic;font-size:15px;line-height:29px;color:#fde6da}
.author{position:absolute;left:334px;top:305px;font-size:15px;font-weight:700;color:var(--white)}
.origin{position:absolute;left:334px;top:330px;font-size:13px;font-style:italic;color:#fde6da}

/* newsletter */
.lead{position:absolute;left:0;width:1200px;text-align:center;font-size:17px;line-height:28px;color:var(--text)}
.subscribe{position:absolute;left:268px;top:3626px;width:662px;height:44px;border-radius:24px;background:var(--white);box-shadow:0 2px 10px rgba(0,0,0,.12)}
.subscribe span{position:absolute;left:26px;top:13px;font-size:14px;color:var(--muted)}
.subscribe b{position:absolute;right:5px;top:2px;width:136px;height:40px;border-radius:22px;background:var(--orange);color:var(--white);font-size:16px;font-weight:600;text-align:center;line-height:40px}

/* footer */
.site-footer{position:absolute;left:0;top:3773px;width:1200px;height:386px;background:var(--black);border-top-right-radius:210px 130px;color:var(--white)}
.site-footer h4{position:absolute;top:84px;font-size:17px;font-weight:500}
.links{position:absolute;top:124px;list-style:none;font-size:13.5px;line-height:28px}
.news{position:absolute;left:88px;width:240px;height:58px}
.news i{position:absolute;left:0;top:0;width:72px;height:58px}
.news b{position:absolute;left:82px;top:6px;font-size:13.5px;font-weight:500}
.news small{position:absolute;left:82px;top:28px;font-size:11px;color:#bdbdbd}
.powered{position:absolute;top:335px;width:100%;text-align:center;font-size:18px;font-weight:700}
.copy{position:absolute;top:366px;width:100%;text-align:center;font-size:12px}
.chat{position:absolute;left:5px;top:4078px;width:86px;height:70px;border-radius:43px 43px 43px 6px;background:var(--amber);color:var(--white);font-size:14px;font-weight:600;text-align:center;padding-top:16px;line-height:18px}
</style>
</head>
<body>

<header class="site-header">
  <div class="brand">VORNA</div>
  <nav class="nav">
    <a class="active" style="left:396px">Home</a>
    <a style="left:482px">Blogs</a>
    <a style="left:560px">Courses</a>
    <a style="left:668px">Contact Us</a>
    <a style="left:786px">About Us</a>
    <a style="left:900px"><svg width="14" height="14" viewBox="0 0 14 14" style="vertical-align:-1px"><circle cx="7" cy="4" r="3.5" fill="#f39a2a"/><path d="M0 14c0-4 3-6 7-6s7 2 7 6z" fill="#f39a2a"/></svg> Sign In</a>
    <span class="sep">|</span>
    <a style="left:1020px"><svg width="14" height="14" viewBox="0 0 14 14" style="vertical-align:-1px"><path d="M2 12l1-4 7-7 3 3-7 7z" fill="#f39a2a"/></svg> Register</a>
  </nav>
</header>

<section class="hero">
  <div class="hero-photo" role="img" aria-label="Person working on a laptop seen from above, with e-learning icons overlaid"></div>
  <h1 class="hero-title">Largest online e-learning resource for<br>data protection &amp; privacy</h1>
  <a class="btn">Get Trained <svg width="17" height="17" viewBox="0 0 16 16"><circle cx="8" cy="8" r="8" fill="#fff"/><path d="M6 4l4 4-4 4" stroke="#e8582a" stroke-width="2" fill="none"/></svg></a>
</section>

<h2 class="section-title" style="top:712px;font-size:37px;line-height:39px">Why the <em>(Privacy Practice Excellence)</em><br>Learning Centre?</h2>

<article class="feature" style="left:88px;top:808px">
  <svg viewBox="0 0 56 56" width="56"><circle cx="28" cy="28" r="25" fill="none" stroke="#e8582a" stroke-width="2.5"/><path d="M28 30l6-14" stroke="#e8582a" stroke-width="3" stroke-linecap="round"/><circle cx="28" cy="30" r="3" fill="#e8582a"/></svg>
  <h3>Comprehensive<br>Roadmap</h3>
  <p>Our objective is to provide a comprehensive competency roadmap, instead of one-off courses, whether you are a new.</p>
</article>
<article class="feature" style="left:438px;top:808px">
  <svg viewBox="0 0 56 56" width="56"><rect x="4" y="16" width="48" height="34" rx="3" fill="none" stroke="#e8582a" stroke-width="2.5"/><path d="M20 16v-7h16v7M4 30h48" stroke="#e8582a" stroke-width="2.5" fill="none"/></svg>
  <h3>Operational<br>Perspective</h3>
  <p>We cover a broad range of data protection topics from both a legal and operational perspective, covering multiple jurisdictions...</p>
</article>
<article class="feature" style="left:787px;top:808px">
  <svg viewBox="0 0 56 56" width="56"><path d="M16 4h24v16a12 12 0 0 1-24 0z" fill="none" stroke="#e8582a" stroke-width="2.5"/><path d="M16 8H8c0 10 6 14 10 14M40 8h8c0 10-6 14-10 14M28 32v10M18 52h20v-10H18z" stroke="#e8582a" stroke-width="2.5" fill="none"/></svg>
  <h3>Academic &amp;<br>International Certification</h3>
  <p>We partner with prominent universities in the region as well as international certification bodies such as the Global Guild of Privacy Practitioners (GGPP).</p>
</article>
<article class="feature" style="left:88px;top:1175px">
  <svg viewBox="0 0 60 56" width="60"><rect x="23" y="4" width="14" height="12" fill="none" stroke="#e8582a" stroke-width="2.5"/><rect x="3" y="38" width="14" height="12" fill="none" stroke="#e8582a" stroke-width="2.5"/><rect x="23" y="38" width="14" height="12" fill="none" stroke="#e8582a" stroke-width="2.5"/><rect x="43" y="38" width="14" height="12" fill="none" stroke="#e8582a" stroke-width="2.5"/><path d="M30 16v22M10 38V27h40v11" stroke="#e8582a" stroke-width="2.5" fill="none"/></svg>
  <h3>Modular Approach &amp;<br>Flexibility</h3>
  <p>All our courses are modular in nature to cater to the busy professional, meaning that you can take the courses separately first at your own pace, and then work your way up.</p>
</article>
<article class="feature" style="left:438px;top:1175px">
  <svg viewBox="0 0 72 56" width="72"><path d="M2 14h12l10 24M70 14H58L48 38M14 16l12-6h10l8 6 6-4h8M24 38l6 6 4-4 4 4 4-4 6-6M26 22l10 8" stroke="#e8582a" stroke-width="2.5" fill="none" stroke-linejoin="round"/></svg>
  <h3>Network with other<br>peers</h3>
  <p>Participate in our online communities and discussion rooms and your network with other like-minded course participants; share best practices, discuss requirements or seek help.</p>
</article>
<article class="feature" style="left:787px;top:1175px">
  <svg viewBox="0 0 56 56" width="56"><path d="M50 6L6 24l18 6 6 18z M24 30L50 6" stroke="#e8582a" stroke-width="2.5" fill="none" stroke-linejoin="round"/></svg>
  <h3>Business and Job<br>Opportunities</h3>
  <p>Collaborate with other professionals on potential business opportunities whether it relates to consultancy, legal or training services.</p>
</article>

<a class="btn" style="left:517px;top:1541px;width:166px;height:48px;font-size:16px">Learn More <svg width="15" height="15" viewBox="0 0 16 16"><circle cx="8" cy="8" r="8" fill="#fff"/><path d="M6 4l4 4-4 4" stroke="#e8582a" stroke-width="2" fill="none"/></svg></a>

<section class="stats-band" role="img" aria-label="Dark blue background of a hand touching a digital e-learning interface">
  <h2>Why Choose Us</h2>
  <p>Our mission at the Privacy Practice Excellence (VORNA) Learning Centre is to provide business and job opportunities, as well as to enhance personal and career advancement for data protection / privacy professionals.</p>
</section>
<div class="stat" style="left:136px;top:1910px"><b>6,375</b><span>ENROLLED STUDENTS</span></div>
<div class="stat" style="left:454px;top:1910px"><b>114</b><span>LESSONS</span></div>
<div class="stat" style="left:772px;top:1910px"><b>169</b><span>VIDEOS</span></div>

<h2 class="section-title" style="top:2284px;font-size:36px">Featured <em>Courses</em></h2>

<article class="course" style="left:288px;background:var(--amber);border-top-left-radius:60px">
  <div class="course-img" role="img" aria-label="Graduation cap resting on books beside a keyboard" style="background:linear-gradient(160deg,#c9a45a,#555 70%,#2c2c2c)"></div>
  <h3>How To Scale Social<br>Impact</h3>
  <div class="rule"></div>
  <div class="price">FREE</div>
  <div class="meta">▪ Dec 19,2019<br>● Mr.Example</div>
</article>
<article class="course" style="left:618px;background:var(--orange);border-bottom-right-radius:120px">
  <div class="course-img" role="img" aria-label="Smartphone with e-learning icons hovering above it" style="height:222px;background:linear-gradient(160deg,#bfc3c7,#6f757c)"></div>
  <h3>Lernix Demonstration<br>Course</h3>
  <div class="rule"></div>
  <div class="price">FREE</div>
  <div class="meta">▪ Dec 19,2019<br>● Mr.Example</div>
</article>
<span class="dot" style="left:586px"></span><span class="dot" style="left:604px"></span>

<section class="testimonials">
  <h2>Testimonials</h2>
  <svg class="abs" style="left:38px;top:257px" width="14" height="20" viewBox="0 0 14 20"><path d="M11 2L3 10l8 8" stroke="#fff" stroke-width="2.5" fill="none"/></svg>
  <svg class="abs" style="left:1148px;top:257px" width="14" height="20" viewBox="0 0 14 20"><path d="M3 2l8 8-8 8" stroke="#fff" stroke-width="2.5" fill="none"/></svg>
  <div class="portrait" role="img" aria-label="Portrait photo of the reviewer"></div>
  <p class="quote">“Lorem ipsum dolor sit amet, consectetur adipiscing elit, sed do eiusmod tempor dunt ut labore et dolore magna aliqua. Ut enim ad minim veniam, quis nostrud exercitation lamco lris nisi ut aliquip ex ea commodo consequat.”</p>
  <div class="author">-Mara Lindqvist</div>
  <div class="origin">USA</div>
</section>

<h2 class="section-title" style="top:3480px;font-size:36px">Subscribe Our <em>Newsletter</em></h2>
<p class="lead" style="top:3538px">Subscribe now and receive weekly newsletter with educational materials,<br>new courses, interesting posts, popular books and much more!</p>
<div class="subscribe"><span>Enter Your Email Address</span><b>Subscribe</b></div>

<footer class="site-footer">
  <h4 style="left:88px">RECENT NEWS</h4>
  <div class="news" style="top:118px"><i role="img" aria-label="Blog thumbnail" style="background:linear-gradient(135deg,#ddd,#777)"></i><b>How To Write Blog</b><small>Dec 18,2019</small></div>
  <div class="news" style="top:205px"><i role="img" aria-label="Stack of books thumbnail" style="background:linear-gradient(135deg,#e0a060,#9a5a2a)"></i><b>Hellow World</b><small>Dec 18,2019</small></div>

  <h4 style="left:376px">USEFULL LINKS</h4>
  <ul class="links" style="left:376px"><li>Home</li><li>Blogs</li><li>Courses</li><li>Contact Us</li><li>About Us</li></ul>

  <h4 style="left:601px">LEGAL</h4>
  <ul class="links" style="left:601px"><li>Terms of Service</li><li>Honor Code</li><li>Privacy Policy</li></ul>

  <h4 style="left:798px">FOLLOW</h4>
  <ul class="links" style="left:798px"><li>▪ Circlebook</li><li>▪ Chirper</li><li>▪ Workline</li><li>▪ Snapgram</li></ul>

  <div class="brand brand-small" style="left:962px;top:80px">VORNA</div>

  <div class="powered"><span style="color:#4aa3df">Lernix</span> &nbsp; <span style="color:var(--orange)">Quodly</span></div>
  <div class="copy">© Copyrights.2020.The Company name</div>
</footer>
<div class="chat">Live<br>Chat</div>

</body>
</html>
```